Chamber of Commerce Web Design Project

We are working with Harborlight Chamber of Commerce. They are a new chamber of commerce forming in SoCal.
Some sites to use for inspiration:
https://brevinmarchamber.org
https://quellford.org
https://www.dorwickhavenchamber.com
https://www.tpchamber.com
https://velmorintcc.org
Thank you for taking the time to consider designing a website for us. We are web developers based in Stockton, CA, USA. Most of our projects go through the same process. Understanding this process may help you win a project with us. We custom-code all of our websites in-house. We don’t have any requirements as to what tools you use for your design, but we prefer Figma files. For any design that we label as four-stars, we send it to the client for review. The client picks the final design they want us to use. Once we complete this process, we will continue to show additional clients all the four-star sites and purchase them later. Your designs will have multiple chances to sell. For better chances of success, we ask that you follow these guidelines.
IMAGES:
If you use any images or icons in the design, we ask that you have a link to the asset so we can purchase the image/icon. Most of the designs we submit do not have the customer’s images on them unless they have some great images. Be creative; show us the feeling you are trying to portray with your image choices. Use any royalty-free site you choose. We subscribe to Adobe and mainly use their images, but we can purchase images outside of Adobe.
PLEASE NOTE: we will not submit designs to clients with watermarks on the images.
FONTS:
We ask that you identify the fonts used in the design. This can be done in a message if you want. We typically use Google Fonts and Adobe Fonts.
CONTENT:
We're always open to different content and ideas. We often submit designs with stock images so the client can see our vision. We typically take pictures after the website launch to use their images with our vision. Lorem Ipsum is fine for paragraphs, but we ask that you write the headers in correct English. We want to be able to show the vision and identify the sections of the website.
INSPIRATION:
We typically add a couple of links in the brief of websites we like to help you get started in your design.
REVISIONS:
We do not often ask for revisions of the designs unless we see something in the design that may not appeal to the client. If there are slight changes that we want to make, we do that in the development process.
FEEDBACK:
We rarely give feedback on designs during the design process. We are working on many website projects and do not have the time to provide feedback. We usually respond if your request is well thought out and asks specific questions, but a note asking “feedback, please” usually goes unanswered.

```html
<!DOCTYPE html>
<html lang="en">
<head>
<meta charset="utf-8">
<title>Harborlight Chamber of Commerce</title>
<link href="https://fonts.googleapis.com/css2?family=Oswald:wght@500;700&family=Poppins:wght@400;500;600;700&display=swap" rel="stylesheet">
<style>
:root{
  --blue:#1a6fe8;
  --blue-dark:#0d57c9;
  --navy:#141b35;
  --yellow:#f9c82e;
  --heading:#4a4a4a;
  --text:#444;
  --light:#f2f6fd;
  --white:#fff;
  --line:#d9dde5;
}
*{margin:0;padding:0;box-sizing:border-box}
html,body{width:1200px;height:5076px;overflow:hidden}
body{font-family:"Poppins",sans-serif;color:var(--text);background:var(--white);position:relative}
.abs{position:absolute}
section,header,footer{position:absolute;left:0;width:1200px}
.heading{font-family:"Oswald",sans-serif;font-weight:700;color:var(--heading);text-transform:uppercase;text-align:center;width:100%;font-size:58px;line-height:1}
.ornament{position:absolute;left:0;width:100%;height:30px;display:flex;justify-content:center;align-items:center;gap:10px}
.ornament span{display:block;width:50px;height:2px;background:var(--blue)}
.ornament i{display:block;width:30px;height:30px;border-radius:50%;background:var(--blue)}
.ornament.light span{background:var(--white)}
.ornament.light i{background:var(--yellow)}
.btn{position:absolute;display:flex;align-items:center;justify-content:center;gap:12px;border-radius:30px;font-weight:600;font-size:19px;text-transform:uppercase}
.btn svg{width:24px;height:14px}
.btn-blue{background:var(--blue);color:var(--white)}
.btn-outline{border:2px solid var(--blue);color:var(--blue);background:var(--white)}
.lead{position:absolute;left:150px;width:900px;text-align:center;font-size:14px;line-height:26.5px;color:var(--text)}
.round-arrow{position:absolute;width:40px;height:40px;border-radius:50%;display:flex;align-items:center;justify-content:center}
.round-arrow svg{width:18px;height:12px}

/* header */
.site-header{top:0;height:118px;background:var(--white)}
.brand{position:absolute;display:flex;align-items:center;gap:10px;color:var(--blue);font-family:"Oswald",sans-serif;font-weight:700;text-transform:uppercase;line-height:1}
.brand-mark{border-radius:50%;background:var(--blue);flex:none}
.site-header .brand{left:69px;top:24px}
.site-header .brand-mark{width:60px;height:60px}
.brand-name b{display:block;font-weight:700}
.contact-chip{position:absolute;top:26px;display:flex;gap:10px;align-items:flex-start}
.chip-icon{width:22px;height:22px;background:var(--blue);border-radius:4px;display:flex;align-items:center;justify-content:center}
.chip-icon svg{width:13px;height:13px}
.contact-chip small{display:block;color:var(--blue);font-size:10.5px;line-height:14px}
.contact-chip span{display:block;font-size:11px;color:#222;line-height:14px}
.join-top{left:999px;top:24px;width:138px;height:38px;font-size:13px}
.main-nav{position:absolute;top:78px;left:0;width:1200px;height:24px}
.main-nav a{position:absolute;transform:translateX(-50%);font-size:11.5px;color:#333;text-decoration:none;text-transform:uppercase;white-space:nowrap}
.main-nav a.active{color:var(--blue)}
.main-nav a.active::after{content:"";position:absolute;left:-8px;right:-8px;top:22px;height:2px;background:var(--blue)}

/* hero */
.hero{top:118px;height:814px}
.hero-photo{position:absolute;inset:0;background:radial-gradient(circle at 30% 40%,#3f7fd6 0%,#1c4fa8 35%,#0e2a66 70%,#08183f 100%)}
.hero-panel{position:absolute;left:465px;top:211px;width:676px;height:430px;border-radius:42px;background:rgba(26,111,232,.88);text-align:center;color:var(--white)}
.hero-panel p{font-family:"Oswald",sans-serif;font-weight:500;font-size:40px;margin-top:56px;line-height:1}
.hero-panel h1{font-family:"Oswald",sans-serif;font-weight:700;font-size:64px;line-height:82px;margin-top:14px;text-transform:uppercase}
.hero .btn-learn{left:228px;top:309px;width:218px;height:56px;background:var(--yellow);color:#1b2a4a;font-size:19px}
.dots{position:absolute;top:719px;left:572px;display:flex;gap:4px}
.dots i{width:12px;height:12px;border-radius:50%;background:#d6dce8}
.dots i:first-child{background:var(--yellow)}

/* mission */
.mission{top:932px;height:605px}

/* quick tiles */
.tiles{top:1537px;height:331px}
.tiles-photo{position:absolute;inset:0;background:linear-gradient(90deg,#121a33 0%,#1f2a4a 45%,#141b35 100%)}
.tile{position:absolute;top:60px;width:220px;text-align:center;color:var(--white)}
.tile .ring{width:156px;height:156px;margin:0 auto;border-radius:50%;border:2px dotted var(--yellow);display:flex;align-items:center;justify-content:center}
.tile .core{width:130px;height:130px;border-radius:50%;background:var(--blue);display:flex;align-items:center;justify-content:center}
.tile .core svg{width:58px;height:58px}
.tile h3{font-size:25px;font-weight:600;text-transform:uppercase;margin-top:20px}

/* featured */
.featured{top:1868px;height:1093px}
.post-date{position:absolute;display:flex;align-items:center;gap:8px;color:var(--blue);font-size:14px}
.post-date svg{width:13px;height:13px}
.post-cat{position:absolute;left:69px;top:307px;font-size:15px;color:#222;text-transform:uppercase}
.post-title{position:absolute;left:69px;top:340px;width:660px;font-size:23px;line-height:30px;font-weight:600;color:#111}
.post-photo{position:absolute;left:71px;top:429px;width:666px;height:493px;background:linear-gradient(180deg,#d8e6ea 0%,#6fb4c4 30%,#4d7d5e 55%,#6d7d66 80%,#8c8f8a 100%)}
.side-post{position:absolute;left:786px;width:351px;height:100px}
.side-thumb{position:absolute;left:0;top:0;width:108px;height:83px}
.side-post p{position:absolute;left:124px;top:0;width:227px;font-size:11.5px;line-height:20px;font-weight:500;color:#111}
.side-post .post-date{left:124px;top:46px;font-size:11px}
.side-post .post-date svg{width:11px;height:11px}
.side-post::after{content:"";position:absolute;left:124px;right:0;top:90px;height:1.5px;background:#9aa0aa}

/* programs */
.programs{top:2961px;height:822px;background:var(--light)}
.program{position:absolute;top:370px;width:240px;text-align:center}
.program .ring{width:158px;height:158px;margin:0 auto;border-radius:50%;border:2px dotted var(--blue);display:flex;align-items:center;justify-content:center}
.program .core{width:132px;height:132px;border-radius:50%;background:var(--blue);display:flex;align-items:center;justify-content:center}
.program .core svg{width:60px;height:60px}
.program h3{font-size:20px;line-height:24px;font-weight:600;color:#111;margin-top:22px}

/* testimonials */
.testimonials{top:3783px;height:543px}
.testimonials-photo{position:absolute;inset:0;background:linear-gradient(120deg,#0b4ac2 0%,#1665e0 45%,#0d57c9 100%)}
.testimonials .heading{color:var(--white)}
.quote-mark{position:absolute;left:167px;top:217px;width:168px;height:137px}
.quote-text{position:absolute;left:358px;top:236px;width:672px;color:var(--white);font-size:14px;line-height:26.5px;text-align:justify;text-align-last:center}
.author{position:absolute;left:483px;top:427px;display:flex;align-items:center;gap:12px}
.avatar{width:52px;height:52px;border-radius:50%;background:linear-gradient(#c9d3e3,#8fa3c2);border:2px solid var(--white)}
.author b{display:block;color:var(--yellow);font-size:21px;font-weight:600;line-height:24px}
.author span{display:block;color:var(--white);font-size:12px}

/* partners */
.partners{top:4326px;height:334px;background:var(--white)}
.partner{position:absolute;top:76px;width:198px;height:198px;border-radius:50%;background:var(--white);box-shadow:0 4px 18px rgba(20,40,80,.15)}
.partner i{position:absolute;left:49px;top:69px;width:100px;height:60px;border-radius:8px;background:#dfe3ea}

/* footer */
.site-footer{top:4660px;height:334px;background:var(--light)}
.site-footer .brand{left:69px;top:155px}
.site-footer .brand-mark{width:70px;height:70px}
.footer-col{position:absolute;top:96px}
.footer-col h4{font-family:"Oswald",sans-serif;font-weight:700;font-size:21px;color:var(--heading);text-transform:uppercase;margin-bottom:28px}
.footer-col ul{list-style:none}
.footer-col li{font-size:13.5px;color:#111;line-height:26.5px;position:relative;padding-left:19px}
.footer-col li::before{content:"";position:absolute;left:0;top:10px;width:7px;height:7px;border-radius:50%;background:var(--blue)}
.contact-row{display:flex;gap:18px;margin-bottom:14px;font-size:13px;line-height:16px;color:#111}
.contact-row .chip-icon{flex:none;margin-top:6px}
.newsletter p{font-size:13px;line-height:16px;color:#111;width:200px}
.newsletter .field{width:197px;height:31px;background:var(--white);border:1px solid var(--line);margin-top:14px}
.newsletter .subscribe{width:98px;height:28px;background:var(--blue);color:var(--white);font-size:10px;font-weight:600;display:flex;align-items:center;justify-content:center;margin-top:16px;text-transform:uppercase}

.bottom-bar{top:4994px;height:82px;background:var(--blue-dark)}
.bottom-bar p{position:absolute;left:69px;top:32px;font-size:12px;color:var(--white)}
.social{position:absolute;top:28px;width:26px;height:26px;background:var(--white);border-radius:3px}
</style>
</head>
<body>

<header class="site-header">
  <div class="brand">
    <i class="brand-mark"></i>
    <div class="brand-name"><b style="font-size:40px">HARBORLIGHT</b><b style="font-size:15px;margin-top:3px">Chamber of Commerce</b></div>
  </div>
  <div class="contact-chip" style="left:676px">
    <div class="chip-icon"><svg viewBox="0 0 24 24"><path fill="#fff" d="M6.6 10.8a15 15 0 0 0 6.6 6.6l2.2-2.2c.3-.3.7-.4 1-.2 1.1.4 2.3.6 3.6.6.6 0 1 .4 1 1V20c0 .6-.4 1-1 1A17 17 0 0 1 3 4c0-.6.4-1 1-1h3.5c.6 0 1 .4 1 1 0 1.3.2 2.5.6 3.6.1.3 0 .7-.2 1z"/></svg></div>
    <div><small>Call Us</small><span>(555) 018-2264</span></div>
  </div>
  <div class="contact-chip" style="left:808px">
    <div class="chip-icon"><svg viewBox="0 0 24 24"><path fill="#fff" d="M2 5h20v14H2z M2 5l10 8 10-8" stroke="#1a6fe8" stroke-width="1.5"/></svg></div>
    <div><small>Email Us</small><span>hello@harborlightchamber.org</span></div>
  </div>
  <div class="btn btn-blue join-top">Join Us</div>
  <nav class="main-nav">
    <a class="active" style="left:532px">Home</a>
    <a style="left:615px">About Us</a>
    <a style="left:721px">What We Do ▾</a>
    <a style="left:818px">Members</a>
    <a style="left:914px">Programs</a>
    <a style="left:1003px">Events</a>
    <a style="left:1097px">Contact Us</a>
  </nav>
</header>

<section class="hero">
  <div class="hero-photo" role="img" aria-label="Photo of large blue industrial pipelines inside a plant"></div>
  <div class="hero-panel">
    <p>Welcome to</p>
    <h1>Harborlight Chamber<br>of Commerce</h1>
    <div class="btn btn-learn">Learn More <svg viewBox="0 0 24 14"><path d="M0 7h22M16 1l6 6-6 6" fill="none" stroke="#1b2a4a" stroke-width="2"/></svg></div>
  </div>
  <div class="dots"><i></i><i></i><i></i><i></i></div>
</section>

<section class="mission">
  <div class="ornament" style="top:91px"><span></span><i></i><span></span></div>
  <h2 class="heading abs" style="top:138px">Our Mission</h2>
  <p class="lead" style="top:243px">Lorem ipsum dolor sit amet, consectetur adipiscing elit. Sed finibus libero sed justo imperdiet condimentum. Nulla elementum ligula sapien, eget finibus massa lobortis vitae. Nunc porta purus id tempus bibendum. Maecenas nec orci facilisis, volutpat quam mattis, bibendum massa. Pellentesque luctus lorem in hendrerit sollicitudin. Aenean mollis suscipit nisi at volutpat. Vestib ulum egestas ultrices velit in tincidunt. Mauris et dui lacinia, convallis felis vel, vehicula ligula. Etiam ac magna non purus pellen tesque elementum. Etiam efficitur vel justo nec malesuada. Sed et magna ac lorem convallis malesuada. Pellentesque habitant morbi tristique senectus et netus et malesuada fames ac turpis egestas. Nulla facilisi. Suspendisse sit amet faucibus urna. Fusce commodo, ante sed cursus venenatis, metus elit ornare est, a accumsan sapien nibh at libero.</p>
  <div class="btn btn-blue" style="left:378px;top:468px;width:217px;height:56px">Learn More <svg viewBox="0 0 24 14"><path d="M0 7h22M16 1l6 6-6 6" fill="none" stroke="#fff" stroke-width="2"/></svg></div>
  <div class="btn btn-outline" style="left:605px;top:468px;width:217px;height:56px">Join Now <svg viewBox="0 0 24 14"><path d="M0 7h22M16 1l6 6-6 6" fill="none" stroke="#1a6fe8" stroke-width="2"/></svg></div>
</section>

<section class="tiles">
  <div class="tiles-photo" role="img" aria-label="Dark toned photo of a business meeting with documents on a desk"></div>
  <div class="tile" style="left:89px">
    <div class="ring"><div class="core"><svg viewBox="0 0 24 24"><rect x="3" y="5" width="18" height="16" rx="2" fill="#fff"/><rect x="3" y="5" width="18" height="4" fill="#dfe9fb"/><path d="M7 3v4M17 3v4" stroke="#fff" stroke-width="2"/><path d="M6 12h3M10.5 12h3M15 12h3M6 15.5h3M10.5 15.5h3M15 15.5h3M6 19h3M10.5 19h3" stroke="#1a6fe8" stroke-width="2"/></svg></div></div>
    <h3>Events</h3>
  </div>
  <div class="tile" style="left:353px">
    <div class="ring"><div class="core"><svg viewBox="0 0 24 24" fill="#fff"><circle cx="12" cy="8" r="3.5"/><path d="M5.5 20c0-4 3-6.5 6.5-6.5s6.5 2.5 6.5 6.5z"/><circle cx="5" cy="9" r="2.5"/><circle cx="19" cy="9" r="2.5"/><path d="M0 17c0-3 2-4.5 5-4.5 1 0 1.8.2 2.4.6A8 8 0 0 0 4.6 17zM24 17c0-3-2-4.5-5-4.5-1 0-1.8.2-2.4.6a8 8 0 0 1 2.8 3.9z"/></svg></div></div>
    <h3>Directory</h3>
  </div>
  <div class="tile" style="left:629px">
    <div class="ring"><div class="core"><svg viewBox="0 0 24 24"><path d="M3 11V4a1 1 0 0 1 1-1h7l10 10-8 8z" fill="#fff"/><circle cx="7.5" cy="7.5" r="1.8" fill="#1a6fe8"/></svg></div></div>
    <h3>Hot Deals</h3>
  </div>
  <div class="tile" style="left:891px">
    <div class="ring"><div class="core"><svg viewBox="0 0 24 24" fill="#fff"><path d="M1 8l4-2 3 8-3 2zM23 8l-4-2-3 8 3 2z"/><path d="M8 8l4-2 3 1 4 0 1 5-3 3-5 4-2-1-3-3 2-2 3 2 2-2-4-4-2 1z"/></svg></div></div>
    <h3>Join Now</h3>
  </div>
</section>

<section class="featured">
  <div class="ornament" style="top:92px"><span></span><i></i><span></span></div>
  <h2 class="heading abs" style="top:135px">Featured Posts</h2>
  <div class="post-date" style="left:69px;top:268px"><svg viewBox="0 0 14 14"><rect x="1" y="2" width="12" height="11" rx="1" fill="none" stroke="#1a6fe8" stroke-width="1.6"/><path d="M1 5h12" stroke="#1a6fe8" stroke-width="1.6"/></svg>Apr 25, 2022</div>
  <p class="post-cat">Lorem ipsum dolor sit amet</p>
  <h3 class="post-title">Lorem ipsum dolor sit amet, consec ipsum&nbsp; tetur elit dol dolor sit amet ipsum</h3>
  <div class="post-photo" role="img" aria-label="Photo of a hillside town with green forested mountains behind"></div>
  <div class="round-arrow" style="left:357px;top:971px;border:2px solid var(--blue)"><svg viewBox="0 0 18 12"><path d="M18 6H2M7 1 2 6l5 5" fill="none" stroke="#1a6fe8" stroke-width="2"/></svg></div>
  <div class="round-arrow" style="left:407px;top:971px;background:var(--blue)"><svg viewBox="0 0 18 12"><path d="M0 6h16M11 1l5 5-5 5" fill="none" stroke="#fff" stroke-width="2"/></svg></div>

  <div class="side-post" style="top:268px"><div class="side-thumb" role="img" aria-label="City skyline photo" style="background:linear-gradient(#9fc3dd,#5d7f6f 60%,#6b6e6a)"></div><p>Lorem ipsum dolor sit amet, consec ipsum tetur elit dol dolor sit amet</p><div class="post-date"><svg viewBox="0 0 14 14"><rect x="1" y="2" width="12" height="11" rx="1" fill="none" stroke="#1a6fe8" stroke-width="1.6"/></svg>Apr 25, 2022</div></div>
  <div class="side-post" style="top:384px"><div class="side-thumb" role="img" aria-label="Photo of business people celebrating" style="background:linear-gradient(#2a2a2a,#a23a2a 55%,#d9a56b)"></div><p>Lorem ipsum dolor sit amet, consec ipsum tetur elit dol dolor sit amet</p><div class="post-date"><svg viewBox="0 0 14 14"><rect x="1" y="2" width="12" height="11" rx="1" fill="none" stroke="#1a6fe8" stroke-width="1.6"/></svg>Apr 25, 2022</div></div>
  <div class="side-post" style="top:498px"><div class="side-thumb" role="img" aria-label="Photo of city towers" style="background:linear-gradient(#c9d9e6,#7f8b8f 55%,#5f6a5e)"></div><p>Lorem ipsum dolor sit amet, consec ipsum tetur elit dol dolor sit amet</p><div class="post-date"><svg viewBox="0 0 14 14"><rect x="1" y="2" width="12" height="11" rx="1" fill="none" stroke="#1a6fe8" stroke-width="1.6"/></svg>Apr 25, 2022</div></div>
  <div class="side-post" style="top:612px"><div class="side-thumb" role="img" aria-label="City skyline photo" style="background:linear-gradient(#9fc3dd,#5d7f6f 60%,#6b6e6a)"></div><p>Lorem ipsum dolor sit amet, consec ipsum tetur elit dol dolor sit amet</p><div class="post-date"><svg viewBox="0 0 14 14"><rect x="1" y="2" width="12" height="11" rx="1" fill="none" stroke="#1a6fe8" stroke-width="1.6"/></svg>Apr 25, 2022</div></div>
  <div class="side-post" style="top:729px"><div class="side-thumb" role="img" aria-label="Photo of business people celebrating" style="background:linear-gradient(#2a2a2a,#a23a2a 55%,#d9a56b)"></div><p>Lorem ipsum dolor sit amet, consec ipsum tetur elit dol dolor sit amet</p><div class="post-date"><svg viewBox="0 0 14 14"><rect x="1" y="2" width="12" height="11" rx="1" fill="none" stroke="#1a6fe8" stroke-width="1.6"/></svg>Apr 25, 2022</div></div>
  <div class="side-post" style="top:843px"><div class="side-thumb" role="img" aria-label="Photo of glass office towers" style="background:linear-gradient(120deg,#dbe7f2,#4d78a8 60%,#2e4f7a)"></div><p>Lorem ipsum dolor sit amet, consec ipsum tetur elit dol dolor sit amet</p><div class="post-date"><svg viewBox="0 0 14 14"><rect x="1" y="2" width="12" height="11" rx="1" fill="none" stroke="#1a6fe8" stroke-width="1.6"/></svg>Apr 25, 2022</div></div>
</section>

<section class="programs">
  <div class="ornament" style="top:93px"><span></span><i></i><span></span></div>
  <h2 class="heading abs" style="top:142px">Our Programs</h2>
  <p class="lead" style="top:249px">Lorem ipsum dolor sit amet, consectetur adipiscing elit. Sed finibus libero sed justo imperdiet condimentum. Nulla elementum ligula sapien, eget finibus massa lobortis vitae. Nunc porta purus id tempus bibendum. Maecenas nec orci facilisis, volutpat quam mattis, bibendum massa. Pellentesque luctus lorem in hendrerit sollicitudin.</p>
  <div class="program" style="left:87px">
    <div class="ring"><div class="core"><svg viewBox="0 0 24 24" fill="#fff"><circle cx="12" cy="6" r="3.2"/><circle cx="12" cy="6" r="1.3" fill="#1a6fe8"/><path d="M1 12l4-2 3 8-3 2zM23 12l-4-2-3 8 3 2z"/><path d="M8 12l4-2 3 1h4l1 4-3 3-4 3-2-1-3-3 2-2 2 2 2-2-3-3-2 1z"/></svg></div></div>
    <h3>Business<br>Education Alliance</h3>
  </div>
  <div class="program" style="left:349px">
    <div class="ring"><div class="core"><svg viewBox="0 0 24 24"><path d="M8 14l-3 8 3-1.5 2 2 2-6M16 14l3 8-3-1.5-2 2-2-6" fill="#fff"/><circle cx="12" cy="9" r="7" fill="#fff"/><circle cx="12" cy="9" r="4.8" fill="none" stroke="#1a6fe8" stroke-width="1.2"/><path d="M12 6l.9 1.9 2 .3-1.5 1.4.4 2L12 10.6l-1.8 1 .4-2-1.5-1.4 2-.3z" fill="#1a6fe8"/></svg></div></div>
    <h3>Certificates<br>of Origin</h3>
  </div>
  <div class="program" style="left:627px">
    <div class="ring"><div class="core"><svg viewBox="0 0 24 24" fill="#fff"><path d="M12 2 2 7v2h20V7z"/><rect x="4" y="10" width="2.5" height="8"/><rect x="8.5" y="10" width="2.5" height="8"/><rect x="13" y="10" width="2.5" height="8"/><rect x="17.5" y="10" width="2.5" height="8"/><rect x="2" y="19" width="20" height="3"/></svg></div></div>
    <h3>Government<br>Relations Council</h3>
  </div>
  <div class="program" style="left:887px">
    <div class="ring"><div class="core"><svg viewBox="0 0 24 24"><path d="M12 1l2.6 2 3.2-.3 1 3.1 2.7 1.8-1 3.1 1 3.1-2.7 1.8-1 3.1-3.2-.3L12 22l-2.6-2-3.2.3-1-3.1-2.7-1.8 1-3.1-1-3.1 2.7-1.8 1-3.1 3.2.3z" fill="#fff"/><path d="M7.5 11.5l3 3 6-6" fill="none" stroke="#1a6fe8" stroke-width="2.2"/></svg></div></div>
    <h3>Talent And<br>Workforce</h3>
  </div>
  <div class="btn btn-blue" style="left:449px;top:670px;width:302px;height:56px">View All Programs <svg viewBox="0 0 24 14"><path d="M0 7h22M16 1l6 6-6 6" fill="none" stroke="#fff" stroke-width="2"/></svg></div>
</section>

<section class="testimonials">
  <div class="testimonials-photo" role="img" aria-label="Blue toned photo of fibre optic cables"></div>
  <div class="ornament light" style="top:79px"><span></span><i></i><span></span></div>
  <h2 class="heading abs" style="top:128px">Our Testimonials</h2>
  <svg class="quote-mark" viewBox="0 0 168 137"><path fill="#f9c82e" d="M0 137V70C0 30 20 5 62 0l6 20C45 28 38 42 38 62h32v75zM98 137V70c0-40 20-65 62-70l6 20c-23 8-30 22-30 42h32v75z"/></svg>
  <p class="quote-text">Lorem ipsum dolor sit amet, conse ctetuer adipiscing elit. Aenean comodo ligula eget dolor. Aenean massa. Cum sociis natoque pen atibus et magnis dis parturient montes, nascetur ridiculus mus. Donec quam felis, ultricies nec, pellentesque eu, pretium quis, sem. Nulla consequat massa quis enim. Donec pede justo, fringilla vel, aliquet nec, vulputate eget, arcu. In enim justo, rhoncus ut, imperdiet a, venenatis vitae, justo. Nullam dictum felis eu pede mollis pretium. Integer tincidunt. Cras dapibus. Vivamus elementum</p>
  <div class="author">
    <div class="avatar" role="img" aria-label="Portrait photo of the reviewer"></div>
    <div><b>Marisol Vance</b><span>Managing Director</span></div>
  </div>
  <div class="round-arrow" style="left:69px;top:315px;background:var(--white)"><svg viewBox="0 0 18 12"><path d="M18 6H2M7 1 2 6l5 5" fill="none" stroke="#1a6fe8" stroke-width="2"/></svg></div>
  <div class="round-arrow" style="left:1093px;top:315px;background:var(--yellow)"><svg viewBox="0 0 18 12"><path d="M0 6h16M11 1l5 5-5 5" fill="none" stroke="#fff" stroke-width="2"/></svg></div>
</section>

<section class="partners">
  <div class="round-arrow" style="left:69px;top:154px;border:2px solid var(--blue)"><svg viewBox="0 0 18 12"><path d="M18 6H2M7 1 2 6l5 5" fill="none" stroke="#1a6fe8" stroke-width="2"/></svg></div>
  <div class="partner" style="left:159px"><i></i></div>
  <div class="partner" style="left:386px"><i></i></div>
  <div class="partner" style="left:610px"><i></i></div>
  <div class="partner" style="left:839px"><i></i></div>
  <div class="round-arrow" style="left:1093px;top:154px;background:var(--blue)"><svg viewBox="0 0 18 12"><path d="M0 6h16M11 1l5 5-5 5" fill="none" stroke="#fff" stroke-width="2"/></svg></div>
</section>

<footer class="site-footer">
  <div class="brand">
    <i class="brand-mark"></i>
    <div class="brand-name"><b style="font-size:46px">HARBORLIGHT</b><b style="font-size:17px;margin-top:3px">Chamber of Commerce</b></div>
  </div>
  <div class="footer-col" style="left:449px">
    <h4>Quick Links</h4>
    <ul><li>About Us</li><li>What We do</li><li>Members</li><li>Programs</li><li>Events</li><li>Contact Us</li></ul>
  </div>
  <div class="footer-col" style="left:652px">
    <h4>Contact Us</h4>
    <div class="contact-row"><div class="chip-icon"><svg viewBox="0 0 24 24"><path fill="#fff" d="M6.6 10.8a15 15 0 0 0 6.6 6.6l2.2-2.2c.3-.3.7-.4 1-.2 1.1.4 2.3.6 3.6.6.6 0 1 .4 1 1V20c0 .6-.4 1-1 1A17 17 0 0 1 3 4c0-.6.4-1 1-1h3.5c.6 0 1 .4 1 1 0 1.3.2 2.5.6 3.6.1.3 0 .7-.2 1z"/></svg></div><div>CALL US<br>012 345 6789</div></div>
    <div class="contact-row"><div class="chip-icon"><svg viewBox="0 0 24 24"><path fill="#fff" d="M2 5h20v14H2z M2 5l10 8 10-8" stroke="#1a6fe8" stroke-width="1.5"/></svg></div><div>EMAIL US<br>info@websitename.com</div></div>
    <div class="contact-row"><div class="chip-icon"><svg viewBox="0 0 24 24"><path fill="#fff" d="M12 2a7 7 0 0 0-7 7c0 5 7 13 7 13s7-8 7-13a7 7 0 0 0-7-7z"/><circle cx="12" cy="9" r="2.5" fill="#1a6fe8"/></svg></div><div>Address line dummy here<br>Address line dummy</div></div>
  </div>
  <div class="footer-col newsletter" style="left:940px">
    <h4>Our Newsletter</h4>
    <p>Subscribe our newsletter to get the latest news.</p>
    <div class="field"></div>
    <div class="subscribe">Subscribe</div>
  </div>
</footer>

<section class="bottom-bar">
  <p>Copyright © 2025 All Rights Reserved By Company Name</p>
  <i class="social" style="left:1015px"></i>
  <i class="social" style="left:1047px"></i>
  <i class="social" style="left:1079px"></i>
  <i class="social" style="left:1111px"></i>
</section>

</body>
</html>
```